Lumora Systems New Website - IT Infrastructure | Smart Cabinet | Micro Data Center

We're an IT SI providing Server Room Design & Build | All-in-One Rack & Smart Cabinet | Structured Cabling | IT Relocation | Maintenance. Old website can be found at www.lumorasys.com.hk. We'd like a brand new wix website which is modern, minimalist, interactive with some animation. Website content will be mostly static and include our service, our project, news and events, about us, contacts, blogs, partners and brands, etc.

reference sites:
We'd like to see more designs referring to below

https://www.pixelvane.example/design/41736205
https://www.pixelvane.example/design/41892417
https://velbrinn.example/

Animation (scrolling effect) referring to
https://velbrinn.example/intelligence/smart-office-room/
Updates

we'd like below style.

Designs look the same

Target Market(s)

Commercials in HK

Industry/Entity Type

IT, Technology, Data Center

Coding

Coded - Design and coding required

Font styles to use
Sans Serif

Requirements
Must have
• CMS, Some Interactive Elements/ Graphics

```html
<!DOCTYPE html>
<html lang="en">
<head>
<meta charset="utf-8">
<title>Lumora Systems — IT Infrastructure | Smart Cabinet | Micro Data Center</title>
<link href="https://fonts.googleapis.com/css2?family=Poppins:wght@400;500;600;700;800&display=swap" rel="stylesheet">
<style>
:root{
  --red:#d9321f;
  --navy:#0c2150;
  --ink:#1b1b1b;
  --night:#101318;
  --mist:#e7edf8;
  --white:#ffffff;
  --grey:#7a7f88;
}
*{margin:0;padding:0;box-sizing:border-box}
html,body{width:1200px;height:4103px;overflow:hidden;background:#fff}
body{font-family:'Poppins',sans-serif;color:var(--ink);position:relative}
.abs{position:absolute}
.btn{position:absolute;background:var(--red);color:#fff;font-size:14px;display:flex;align-items:center;justify-content:center;letter-spacing:.3px;text-transform:uppercase}
.section-title{position:absolute;left:0;width:1200px;text-align:center;color:var(--red);font-weight:700;font-size:37px;letter-spacing:.3px}

/* header & hero */
.hero-photo{position:absolute;left:0;top:0;width:1200px;height:690px;background:radial-gradient(ellipse at 60% 40%,#3a4656 0%,#1d2630 45%,#0b1118 100%)}
.brand{position:absolute;display:flex;align-items:center;gap:12px;font-weight:600;font-size:27px;color:#fff}
.brand .mark{width:30px;height:30px;border:3px solid #fff;border-radius:4px}
.nav{position:absolute;top:0;left:0;width:1200px;height:104px;background:rgba(255,255,255,.06);border-bottom:1px solid rgba(255,255,255,.08)}
.nav a{position:absolute;top:28px;color:#fff;font-size:15px;text-decoration:none}
.hero-line{position:absolute;left:110px;color:#fff;font-weight:700;font-size:35px;letter-spacing:.3px}

/* about */
.about-photo{position:absolute;left:0;top:686px;width:1200px;height:525px;background:linear-gradient(180deg,#fff 0%,#f1f4fa 35%,#e3e8f2 100%);clip-path:polygon(0 0,100% 0,100% 75%,50% 100%,0 75%)}
.about-kicker{position:absolute;left:110px;top:858px;font-size:20px;color:#2a2a2a}
.about-title{position:absolute;left:110px;top:895px;font-size:39px;font-weight:700;color:var(--red)}
.about-text{position:absolute;left:615px;top:796px;width:470px;font-size:15.5px;line-height:29px;color:#2a2a2a}

/* services */
.svc{position:absolute;top:1368px;width:220px}
.svc .frame-a{position:absolute;left:-11px;top:0;width:190px;height:130px;border-left:2px solid #222;border-top:2px solid #222}
.svc .frame-b{position:absolute;left:20px;top:60px;width:190px;height:110px;border-right:2px solid var(--red);border-bottom:2px solid var(--red)}
.svc .pic{position:absolute;left:0;top:11px;width:199px;height:148px}
.svc .label{position:absolute;left:-10px;top:184px;width:230px;text-align:center;font-weight:700;font-size:14.5px;line-height:22px;text-transform:uppercase}
.round{position:absolute;width:44px;height:44px;border-radius:50%;background:#fff;box-shadow:0 4px 12px rgba(0,0,0,.14);display:flex;align-items:center;justify-content:center}
.round.on{background:var(--red)}

/* projects */
.proj-pic{position:absolute;top:1902px;width:192px;height:193px;border-radius:10px}
.proj-label{position:absolute;top:2122px;width:230px;text-align:center;color:#fff;font-weight:700;font-size:15.5px;line-height:22px;text-transform:uppercase}

/* partners */
.pill{position:absolute;width:212px;height:96px;border-radius:48px;background:#fff;box-shadow:0 5px 16px rgba(0,0,0,.13);display:flex;align-items:center;justify-content:center}
.pill span{display:block;width:110px;height:22px;border-radius:11px;background:#d4d8de}

/* news */
.news{position:absolute;top:3097px;width:306px}
.news .pic{width:306px;height:204px;position:relative}
.news .date{position:absolute;left:0;top:16px;background:#1c1c1c;color:#fff;font-size:15px;padding:4px 12px}
.news h3{margin-top:20px;font-size:16.5px;font-weight:700;text-transform:uppercase}
.news p{margin-top:6px;font-size:15px;line-height:22px;color:#2a2a2a}

/* footer */
.footer{position:absolute;left:0;top:3606px;width:1200px;height:497px;background:radial-gradient(ellipse at 50% 80%,#2a2d33 0%,#121418 60%,#0b0c0f 100%)}
.f-text{position:absolute;color:#fff;font-size:15px}
.field{position:absolute;left:787px;width:300px;height:35px;background:#fff;color:#8a8e95;font-size:14.5px;padding:6px 24px}
</style>
</head>
<body>

<!-- HERO -->
<div class="hero-photo" role="img" aria-label="Dim server room aisle with racks of blinking servers"></div>
<svg class="abs" style="left:0;top:0" width="1200" height="700" viewBox="0 0 1200 700">
  <polygon points="1200,110 1200,690 250,690 1168,652" fill="var(--red)"/>
  <polygon points="0,686 1160,655 1200,655 1200,700 0,700" fill="#fff"/>
  <polygon points="1160,655 1168,652 250,690 0,690 0,686" fill="#fff"/>
</svg>
<div class="nav">
  <div class="brand" style="left:112px;top:31px"><span class="mark"></span>Lumora</div>
  <a style="left:681px">Home</a>
  <a style="left:764px">About Us</a>
  <a style="left:869px">Our Projects</a>
  <a style="left:999px">Contact Us</a>
</div>
<div class="hero-line" style="top:236px">IT INFRASTRUCTURE</div>
<div class="hero-line" style="top:304px">SMART CABINET</div>
<div class="hero-line" style="top:373px">MICRO DATA CENTER</div>
<div class="btn" style="left:110px;top:448px;width:131px;height:43px">Get Started</div>
<svg class="abs" style="left:530px;top:274px" width="138" height="138" viewBox="0 0 138 138">
  <circle cx="69" cy="69" r="67" fill="rgba(255,255,255,.25)"/>
  <circle cx="69" cy="69" r="52" fill="#e8e8ea"/>
  <circle cx="69" cy="69" r="42" fill="var(--red)"/>
  <polygon points="58,48 58,90 92,69" fill="#fff"/>
</svg>

<!-- ABOUT -->
<div class="about-photo" role="img" aria-label="Bright pale data center corridor fading into white"></div>
<div class="about-kicker">ABOUT US</div>
<div class="about-title">LUMORA SYSTEMS</div>
<p class="about-text">Lumora Systems is well experienced in delivering the best in Data Center Infrastructure, Network Infrastructure, Structured Cabling, Telephony, Access Control, Video Surveillance, Audiovisual &amp; Conferencing, Relocation &amp; Migration and Maintenance solutions. Our dedication, focus, and expertise wins much recognition of many IT professionals in all industries in the region. In Lumora</p>
<div class="btn" style="left:615px;top:1017px;width:129px;height:41px">Read More</div>

<!-- SERVICES -->
<div class="section-title" style="top:1290px">OUR SERVICES</div>

<div class="svc" style="left:128px">
  <div class="frame-a"></div><div class="frame-b"></div>
  <div class="pic" role="img" aria-label="Blue-lit data center hall with server racks" style="background:linear-gradient(135deg,#0d2d6b,#2a86d4 50%,#0a1d45)"></div>
  <div class="label">Data Center<br>Design and Build</div>
</div>
<div class="svc" style="left:379px">
  <div class="frame-a"></div><div class="frame-b"></div>
  <div class="pic" role="img" aria-label="Server racks glowing blue and orange with cabling" style="background:linear-gradient(135deg,#0b2550,#1f7fc8 45%,#c2571f 80%,#0b1c3c)"></div>
  <div class="label">Structured Cabling<br>and Fiber Backbon</div>
</div>
<div class="svc" style="left:630px">
  <div class="frame-a"></div><div class="frame-b"></div>
  <div class="pic" role="img" aria-label="Colourful network patch cables plugged into a switch" style="background:linear-gradient(135deg,#1a3c7a,#3aa35a 35%,#d24a2a 65%,#6a2b8c)"></div>
  <div class="label" style="top:187px">All-in-one Rack /<br>Micro-Data Center</div>
</div>
<div class="svc" style="left:878px">
  <div class="frame-a"></div><div class="frame-b"></div>
  <div class="pic" role="img" aria-label="Modern conference room with long table and chairs" style="background:linear-gradient(180deg,#1e2226,#4a4c4e 55%,#8a8378)"></div>
  <div class="label">Audiovisual and<br>Conference Room</div>
</div>

<svg width="0" height="0" style="position:absolute"><defs>
  <symbol id="arrow-r" viewBox="0 0 20 12"><path d="M1 6h17M13 1l5 5-5 5" fill="none" stroke="currentColor" stroke-width="1.8" stroke-linecap="round" stroke-linejoin="round"/></symbol>
</defs></svg>
<div class="round" style="left:203px;top:1613px;color:#111"><svg width="20" height="12"><use href="#arrow-r"/></svg></div>
<div class="round on" style="left:456px;top:1613px;color:#fff"><svg width="20" height="12"><use href="#arrow-r"/></svg></div>
<div class="round" style="left:705px;top:1613px;color:#111"><svg width="20" height="12"><use href="#arrow-r"/></svg></div>
<div class="round" style="left:955px;top:1613px;color:#111"><svg width="20" height="12"><use href="#arrow-r"/></svg></div>

<!-- PROJECTS -->
<svg class="abs" style="left:0;top:1740px" width="1200" height="570" viewBox="0 0 1200 570">
  <polygon points="0,40 1200,0 1200,565 0,565" fill="var(--red)"/>
  <polygon points="0,0 600,0 40,30 0,60" fill="#fff"/>
  <polygon points="30,48 1200,8 1190,550 0,562" fill="var(--navy)"/>
  <polygon points="1200,555 300,570 1200,570" fill="#fff"/>
</svg>
<div class="section-title" style="top:1828px;color:#fff">OUR PROJECTS</div>
<div class="proj-pic" style="left:113px" role="img" aria-label="Analyst working at screens of financial data" data-tone="warm" ></div>
<div class="proj-pic" style="left:507px" role="img" aria-label="Container port at dusk overlaid with network lines"></div>
<div class="proj-pic" style="left:899px" role="img" aria-label="Modern glass office tower under blue sky"></div>
<style>
.proj-pic:nth-of-type(1){}
</style>
<div class="abs" style="left:113px;top:1902px;width:192px;height:193px;border-radius:10px;background:linear-gradient(135deg,#3a2a22,#b8712e 45%,#233a5c)"></div>
<div class="abs" style="left:507px;top:1902px;width:192px;height:193px;border-radius:10px;background:linear-gradient(180deg,#5d7895,#2c3f57 50%,#141e2c)"></div>
<div class="abs" style="left:899px;top:1902px;width:192px;height:193px;border-radius:10px;background:linear-gradient(180deg,#6fa6e8,#3d5fb8 55%,#9fb2d8)"></div>
<svg class="abs" style="left:340px;top:1960px" width="130" height="70" viewBox="0 0 130 70">
  <path d="M4 60 C30 70 40 10 70 8 C95 6 105 30 120 40" fill="none" stroke="#fff" stroke-width="2" stroke-dasharray="6 5"/>
  <path d="M110 40 L121 41 L118 30" fill="none" stroke="#fff" stroke-width="2"/>
</svg>
<svg class="abs" style="left:737px;top:1960px" width="130" height="70" viewBox="0 0 130 70">
  <path d="M4 60 C30 70 40 10 70 8 C95 6 105 30 120 40" fill="none" stroke="#fff" stroke-width="2" stroke-dasharray="6 5"/>
  <path d="M110 40 L121 41 L118 30" fill="none" stroke="#fff" stroke-width="2"/>
</svg>
<div class="proj-label" style="left:94px">A Renowned China<br>Based Listed<br>Insurance Company</div>
<div class="proj-label" style="left:488px;top:2137px">Meridian Trade</div>
<div class="proj-label" style="left:880px">A Renowned<br>China Based<br>Securities Firm</div>
<svg class="abs" style="left:58px;top:2009px" width="24" height="24" viewBox="0 0 24 24"><circle cx="12" cy="12" r="10.5" fill="none" stroke="#fff" stroke-width="1.6"/><path d="M14 7l-5 5 5 5" fill="none" stroke="#fff" stroke-width="1.8"/></svg>
<svg class="abs" style="left:1118px;top:2009px" width="24" height="24" viewBox="0 0 24 24"><circle cx="12" cy="12" r="10.5" fill="none" stroke="#fff" stroke-width="1.6"/><path d="M10 7l5 5-5 5" fill="none" stroke="#fff" stroke-width="1.8"/></svg>

<!-- PARTNERS -->
<div class="section-title" style="top:2384px">OUR PARTNERS</div>
<div class="pill" style="left:-129px;top:2498px"><span></span></div>
<div class="pill" style="left:112px;top:2498px"><span></span></div>
<div class="pill" style="left:365px;top:2498px"><span></span></div>
<div class="pill" style="left:618px;top:2498px"><span></span></div>
<div class="pill" style="left:872px;top:2498px"><span></span></div>
<div class="pill" style="left:112px;top:2627px"><span></span></div>
<div class="pill" style="left:365px;top:2627px"><span></span></div>
<div class="pill" style="left:618px;top:2627px"><span></span></div>
<div class="pill" style="left:872px;top:2627px"><span></span></div>
<div class="pill" style="left:1127px;top:2627px"><span></span></div>
<div class="round" style="left:542px;top:2777px;width:42px;height:42px;color:#111"><svg width="20" height="12" style="transform:scaleX(-1)"><use href="#arrow-r"/></svg></div>
<div class="round on" style="left:620px;top:2777px;width:42px;height:42px;color:#fff"><svg width="20" height="12"><use href="#arrow-r"/></svg></div>

<!-- NEWS -->
<div class="abs" style="left:0;top:2920px;width:1200px;height:686px;background:var(--mist)"></div>
<div class="section-title" style="top:2998px">OUR NEWS</div>
<div class="news" style="left:112px">
  <div class="pic" role="img" aria-label="Two engineers reviewing a tablet beside server racks" style="background:linear-gradient(135deg,#2a2f36,#8a7a68 55%,#d8d2c8)"><div class="date">Posted On Oct 14 2023</div></div>
  <h3>Lorem Ipsum</h3>
  <p>Lorem ipsum dolor sit amet, consectetur adipiscing elit, sed do eiusmod tempor incididunt ut labore et dolore magna aliqua. Ut enim ad minim veniam, quis nostrud</p>
</div>
<div class="news" style="left:446px">
  <div class="pic" role="img" aria-label="Colleagues talking in a bright server room" style="background:linear-gradient(135deg,#3a3e44,#a89c8c 55%,#e6e2da)"><div class="date">Posted On Oct 14 2023</div></div>
  <h3>Lorem Ipsum</h3>
  <p>Lorem ipsum dolor sit amet, consectetur adipiscing elit, sed do eiusmod tempor incididunt ut labore et dolore magna aliqua. Ut enim ad minim veniam, quis nostrud</p>
</div>
<div class="news" style="left:781px">
  <div class="pic" role="img" aria-label="Technician holding a laptop in a data center aisle" style="background:linear-gradient(135deg,#1b2b4a,#3c6db0 45%,#c9cdd4)"><div class="date">Posted On Oct 14 2023</div></div>
  <h3>Lorem Ipsum</h3>
  <p>Lorem ipsum dolor sit amet, consectetur adipiscing elit, sed do eiusmod tempor incididunt ut labore et dolore magna aliqua. Ut enim ad minim veniam, quis nostrud</p>
</div>
<div class="btn" style="left:112px;top:3481px;width:129px;height:39px">Read More</div>
<div class="btn" style="left:446px;top:3481px;width:129px;height:39px">Read More</div>
<div class="btn" style="left:781px;top:3481px;width:129px;height:39px">Read More</div>

<!-- FOOTER -->
<div class="footer"></div>
<div class="brand" style="left:112px;top:3700px"><span class="mark"></span>Lumora</div>
<div class="f-text" style="left:110px;top:3768px;line-height:34.5px">Rm 908, 9/F, Harbourgate Centre,<br>12 Lantern Road,<br>Kwun Tong, Kowloon,<br>Hong Kong</div>
<div class="f-text" style="left:442px;top:3696px"><b>Email:</b> marketing@lumorasys.com.hk</div>
<div class="f-text" style="left:442px;top:3731px"><b>Phone:</b> +852 2000 4410 / +852 5000 7381</div>
<div class="f-text" style="left:442px;top:3765px"><b>Fax:</b> +852 2000 4499</div>
<svg class="abs" style="left:442px;top:3805px" width="30" height="30" viewBox="0 0 30 30"><circle cx="15" cy="15" r="13" fill="none" stroke="var(--red)" stroke-width="2"/><path d="M11 9c1 0 2 3 1 4 1 2 3 4 5 5 1-1 4 0 4 1 0 2-2 3-4 2-4-1-8-5-9-9 0-2 1-3 3-3z" fill="var(--red)"/></svg>
<div class="f-text" style="left:481px;top:3808px">Instant Chat</div>
<svg class="abs" style="left:442px;top:3856px" width="30" height="30" viewBox="0 0 30 30"><circle cx="15" cy="15" r="13" fill="none" stroke="var(--red)" stroke-width="2"/><path d="M11 9c1 0 2 3 1 4 1 2 3 4 5 5 1-1 4 0 4 1 0 2-2 3-4 2-4-1-8-5-9-9 0-2 1-3 3-3z" fill="var(--red)"/></svg>
<div class="f-text" style="left:481px;top:3859px">Instant Chat</div>
<div class="field" style="top:3698px">Name</div>
<div class="field" style="top:3744px">Enail</div>
<div class="field" style="top:3789px">Subject</div>
<div class="field" style="top:3833px;height:69px">Message</div>
<div class="btn" style="left:960px;top:3911px;width:127px;height:40px">Submit</div>
<div class="f-text" style="left:0;width:1200px;text-align:center;top:4027px">© 2023 by Lumora Systems</div>

</body>
</html>
```